Design website home page for pathology consulting company

Starting a new consulting company with anatomic pathologists focused on expert diagnosis and second opinions on difficult pathology cases. In the near future we will be incorporating next generation diagnostics for rare diseases of childhood into the business. These include discovery and testing of DNA for mutations.

The company is formed around one of the best known pathologists in the world named Marcel "Biscuit" Trowell. The name of the company is "BiscuitLab"

We had a logo design by SketchForum - it is great. I will attach file as soon as I have it (contest ending today). Our company is medical, uses microscopes, DNA, probably will focus on childhood diseases but not solely on childhood diseases. we're not particularly conservative, but the customers we want to appeal to include older practicing pathologists as well as patients (sometimes parents) looking for second opinions.

Think a group of expert doctors diagnosing disease through the microscope and through DNA technology, ages ranging from 35-75 all trained by the best pathologist in the world - "Biscuit"

We receive glass slides from diseases from patients all over the world from docs who need an expert to tell them what is the diagnosis. So "path to the diagnosis" is also part of the company marketing message.

We want the website design to describe our company but be very simple to find what one is looking for as we will use it as the launch page to:
1) order services
2) check results/reports
3) set up new account
4) speak with one of the pathologists
5) see our test menu
6) access our educational material/webinars
Updates

Update - looking for home page design and then finalists will ask for second page design to keep with theme - ok?

Reason: realized this project isn't web design but web home page design - thanks

Reason: Holidays for some in next two weeks

Reason: Hot discussion among collaborators for a few of the submissions. Will provide detail individually this weekend. Thanks so much for all the submissions!

Target Market(s)

Referring pathologists, physicians who want second opinions on pathology disease diagnosis, patients who have had biopsies (either patients themselves or parents of patients), generally high education level

Industry/Entity Type

Marketing

Requirements
Must have
• BiscuitLab
Next Generation Pathology Consultants

```html
<!DOCTYPE html>
<html lang="en">
<head>
<meta charset="utf-8">
<title>BiscuitLab – Next Generation Pathology Consultants</title>
<link href="https://fonts.googleapis.com/css2?family=Open+Sans:wght@400;600;700&display=swap" rel="stylesheet">
<style>
:root{
  --blue:#1f6fbf;
  --blue-deep:#0b64ad;
  --blue-tab:#3a7fcf;
  --ink:#333333;
  --text:#6a6a6a;
  --muted:#7d7d7d;
  --rule:#e3e3e3;
  --canvas-top:#ececec;
  --white:#ffffff;
  --black:#0a0a0a;
  --panel-grey:#7b7b7b;
  --btn-dark:#2f3340;
}
*{margin:0;padding:0;box-sizing:border-box}
html,body{width:1200px;height:1079px;overflow:hidden}
body{position:relative;font-family:"Open Sans",Arial,sans-serif;background:var(--white);color:var(--text)}
.top-band{position:absolute;left:0;top:0;width:1200px;height:515px;background:var(--canvas-top)}
.footer-band{position:absolute;left:0;top:1013px;width:1200px;height:66px;background:var(--black)}

/* brand */
.brand{position:absolute;left:100px;top:12px;width:170px;text-align:center}
.brand-dot{width:64px;height:64px;border-radius:50%;background:#9ca3ab;margin:0 auto 4px}
.brand-name{font-size:25px;font-weight:600;color:var(--blue-deep);letter-spacing:.5px;line-height:28px}
.brand-tag{font-size:8.5px;color:var(--muted);line-height:11px}

/* utility */
.utility{position:absolute;right:99px;top:47px;display:flex;font-size:12px;color:var(--muted)}
.utility a{color:var(--muted);text-decoration:none;display:flex;align-items:center;gap:4px;padding:0 10px;border-left:1px solid #cfcfcf}
.utility a:first-child{border-left:none}
.utility a:last-child{padding-right:0}
.order-line{position:absolute;right:99px;top:74px;font-size:16px;font-weight:700;color:var(--ink)}
.order-line span{color:var(--blue);font-size:17px;margin-left:4px}

/* shell */
.shell{position:absolute;left:99px;top:135px;width:1002px;height:905px;background:var(--white);border-radius:6px;box-shadow:0 0 3px rgba(0,0,0,.12)}
.main-nav{position:absolute;left:99px;top:136px;width:1002px;height:40px;display:flex;background:linear-gradient(#c9c9c9,#a4a4a4);border-radius:5px 5px 0 0;overflow:hidden}
.main-nav a{flex:none;height:40px;line-height:39px;text-align:center;color:var(--white);font-size:13px;font-weight:600;text-decoration:none;border-left:1px solid #d6d6d6}
.main-nav a.active{background:var(--blue-tab);border-left:none}

/* hero */
.hero{position:absolute;left:117px;top:193px;width:966px;height:310px;background:linear-gradient(90deg,#f3f3f2 0%,#e9ecee 40%,#b9b4a8 62%,#3a3a3a 80%,#1c1c1c 100%)}
.hero-photo{position:absolute;inset:0}
.hero-copy{position:absolute;left:29px;top:44px;width:400px}
.hero-title{font-size:29px;font-weight:600;line-height:34px;color:var(--blue)}
.hero-title .lead{color:#3b3b3b}
.hero-text{margin-top:12px;font-size:12px;line-height:21px;color:#6a6a6a;width:335px}
.btn-discover{display:inline-block;margin-top:17px;background:#111;color:var(--white);font-size:13px;font-weight:600;padding:0 19px;height:35px;line-height:35px;border:1px solid #444}

/* focus cards */
.focus-card{position:absolute;top:522px;width:307px;height:115px;border:1px solid #d4d4d4;border-radius:0 0 8px 8px;background:var(--white)}
.focus-tab{position:absolute;left:-1px;top:-1px;height:36px;line-height:36px;padding:0 0 0 14px;color:var(--white);font-size:17px;font-weight:600;background:var(--blue-tab);clip-path:polygon(0 0,100% 0,calc(100% - 10px) 100%,0 100%)}
.focus-text{position:absolute;left:15px;top:51px;width:250px;font-size:11.5px;font-weight:600;line-height:16px;color:var(--ink)}
.focus-play{position:absolute;right:16px;bottom:6px}

/* columns */
.col-heading{font-size:16px;font-weight:600;color:var(--blue);text-transform:uppercase;line-height:20px}
.services{position:absolute;left:117px;top:659px;width:195px}
.services ul{list-style:none;margin-top:9px}
.services li{height:30px;line-height:29px;font-size:11px;color:var(--muted);border-bottom:1px solid #ececec;padding-left:19px;position:relative}
.services li:last-child{border-bottom:none}
.services li::before{content:"";position:absolute;left:1px;top:10px;border-left:6px solid #666;border-top:4px solid transparent;border-bottom:4px solid transparent}
.divider{position:absolute;top:661px;width:1px;height:352px;background:var(--rule)}
.welcome{position:absolute;left:361px;top:659px;width:465px}
.welcome p{font-size:12.5px;line-height:21px;color:var(--muted);margin-top:10px}
.welcome p + p{margin-top:21px}
.welcome h2 + p{margin-top:10px}
.welcome p + h2{margin-top:24px}

/* account panel */
.account{position:absolute;left:864px;top:662px;width:219px;height:357px;border-radius:8px;background:var(--panel-grey);overflow:hidden}
.account-form{height:242px;background:var(--blue-deep);padding:14px 18px 0 18px}
.account-form h3{font-size:16px;font-weight:400;color:var(--white)}
.field{display:block;width:184px;height:32px;margin-top:22px;background:var(--white);border:1px solid #cfcfcf;font:11px "Open Sans",sans-serif;color:#888;padding:0 12px;line-height:30px}
.field + .field{margin-top:23px}
.btn-signup{display:block;width:132px;height:30px;margin:25px 0 0 26px;background:var(--btn-dark);color:var(--white);font-size:14px;text-align:center;line-height:30px}
.forgot{display:block;text-align:center;color:var(--white);font-size:11px;margin-top:8px}
.btn-menu{position:absolute;left:19px;top:260px;width:182px;height:30px;background:linear-gradient(#3a3a3a,#0d0d0d);color:var(--white);font-size:14px;font-weight:600;text-align:center;line-height:30px}
.btn-speak{position:absolute;left:19px;top:307px;width:182px;height:30px;background:linear-gradient(#ffffff,#e4e4e4);color:#333;font-size:14px;font-weight:600;text-align:center;line-height:30px}

/* footer */
.copyright{position:absolute;left:99px;top:1050px;font-size:12px;color:var(--white)}
.social{position:absolute;right:99px;top:1049px;display:flex;gap:10px}
.social span{width:18px;height:18px;border-radius:50%;background:var(--white)}
</style>
</head>
<body>
<div class="top-band"></div>
<div class="footer-band"></div>

<header>
  <div class="brand">
    <div class="brand-dot"></div>
    <div class="brand-name">BiscuitLab</div>
    <div class="brand-tag">Next Generation Pathology Consultants</div>
  </div>
  <nav class="utility">
    <a href="#"><svg width="9" height="11" viewBox="0 0 9 11"><path d="M1 .5h5l2.5 2.5v7.5h-7.5z" fill="none" stroke="#555"/><path d="M2.5 5h4M2.5 7h4" stroke="#555"/></svg>Register</a>
    <a href="#"><svg width="12" height="11" viewBox="0 0 12 11"><circle cx="6" cy="3" r="2.8" fill="#3a6ea8"/><path d="M0.5 11c0-3.5 2.5-4.8 5.5-4.8s5.5 1.3 5.5 4.8z" fill="#3a6ea8"/></svg>Sign In</a>
    <a href="#"><svg width="13" height="11" viewBox="0 0 13 11"><path d="M1 4c0-3 11-3 11 0v1.3H9.3V3.8H3.7v1.5H1z" fill="#3a6ea8"/><rect x="2.5" y="6" width="8" height="4.5" rx="1" fill="#3a6ea8"/></svg>contact</a>
  </nav>
  <div class="order-line">24/7 ORDER <span>080-5550-146</span></div>
</header>

<div class="shell"></div>

<nav class="main-nav">
  <a href="#" class="active" style="width:90px">Home</a>
  <a href="#" style="width:131px">About Us</a>
  <a href="#" style="width:121px">Services</a>
  <a href="#" style="width:201px">Pathology Consultants</a>
  <a href="#" style="width:112px">Patients</a>
  <a href="#" style="width:111px">Results</a>
  <a href="#" style="width:121px">Accounts</a>
  <a href="#" style="width:115px">Contact Us</a>
</nav>

<section class="hero">
  <div class="hero-photo" role="img" aria-label="Close-up photograph of a laboratory microscope with objective lenses"></div>
  <div class="hero-copy">
    <h1 class="hero-title"><span class="lead">BiscuitLab</span> Next Generation Pathology Consultants</h1>
    <p class="hero-text">Sed ut perspiciatis unde omnis iste natus error sit voluptatem accusantium doloremque laudantium, totam rem aperiam, eaque ipsa quae ab illo inventore veritatis et quasi architecto beatae vitae dicta sunt explicabo.</p>
    <a class="btn-discover">Discover More</a>
  </div>
</section>

<article class="focus-card" style="left:117px">
  <div class="focus-tab" style="width:259px">Surgical/Autopsy Pathology</div>
  <p class="focus-text">Pathologic examination of surgical tissue specimens constitutes the major.</p>
  <svg class="focus-play" width="38" height="38" viewBox="0 0 38 38"><circle cx="19" cy="19" r="18" fill="#2a7fd4"/><circle cx="19" cy="19" r="15" fill="none" stroke="#fff" stroke-width="1.5"/><path d="M15 11l11 8-11 8z" fill="#fff"/></svg>
</article>
<article class="focus-card" style="left:447px">
  <div class="focus-tab" style="width:209px">Cytopathology</div>
  <p class="focus-text">The cytopathology laboratory at BiscuitLab Consultants is a full service.</p>
  <svg class="focus-play" width="38" height="38" viewBox="0 0 38 38"><circle cx="19" cy="19" r="18" fill="#2a7fd4"/><circle cx="19" cy="19" r="15" fill="none" stroke="#fff" stroke-width="1.5"/><path d="M15 11l11 8-11 8z" fill="#fff"/></svg>
</article>
<article class="focus-card" style="left:777px">
  <div class="focus-tab" style="width:209px">Hematopathology</div>
  <p class="focus-text" style="width:280px">Pathologic examination of all hematolymphoid tissue specimens is performed.</p>
  <svg class="focus-play" width="38" height="38" viewBox="0 0 38 38"><circle cx="19" cy="19" r="18" fill="#2a7fd4"/><circle cx="19" cy="19" r="15" fill="none" stroke="#fff" stroke-width="1.5"/><path d="M15 11l11 8-11 8z" fill="#fff"/></svg>
</article>

<section class="services">
  <h2 class="col-heading">Our Services</h2>
  <ul>
    <li>Autopsy Pathology</li>
    <li>Bone and Soft Tissue Pathology</li>
    <li>Clinically Interactive Consultative</li>
    <li>Dermatopathology</li>
    <li>Forensic Pathology</li>
    <li>Gastrointestinal &amp; Hepatic</li>
    <li>Hematology &amp; Hemato</li>
    <li>Immunopathology/Histopathology</li>
    <li>Pediatric Pathology</li>
    <li>Surgical Pathology</li>
    <li>Urologic Pathology</li>
  </ul>
</section>
<div class="divider" style="left:339px"></div>
<div class="divider" style="left:847px"></div>

<section class="welcome">
  <h2 class="col-heading">Welcome to BiscuitLab</h2>
  <p>Sed ut perspiciatis unde omnis iste natus error sit voluptatem accusantium doloremque laudantium, totam rem aperiam, eaque ipsa quae ab illo inventore veritatis et quasi architecto beatae vitae dicta sunt explicabo.</p>
  <p>Nemo enim ipsam voluptatem quia voluptas sit aspernatur aut odit aut fugit, sed quia consequuntur.</p>
  <h2 class="col-heading">We Work for Your Health</h2>
  <p>Sed ut perspiciatis unde omnis iste natus error sit voluptatem accusantium doloremque laudantium, totam rem aperiam, eaque ipsa quae ab illo inventore veritatis et quasi architecto beatae vitae dicta sunt explicabo.</p>
  <p>Nemo enim ipsam voluptatem quia voluptas sit aspernatur aut odit aut fugit, sed quia consequuntur magni dolores eos qui ratione voluptatem sequi nesciunt. Neque porro quisquam est, qui dolorem ipsum.</p>
</section>

<aside class="account">
  <div class="account-form">
    <h3>Setup New Account</h3>
    <span class="field">Enter your email</span>
    <span class="field">Enter password</span>
    <a class="btn-signup">SIGN UP</a>
    <a class="forgot">Forgot Password?</a>
  </div>
  <a class="btn-menu">See Our Test Menu</a>
  <a class="btn-speak">Speek with Pathologist</a>
</aside>

<footer>
  <p class="copyright">Copyright © 2013 BiscuitLab, Inc . All Rights Reserved</p>
  <div class="social" aria-label="Social links"><span></span><span></span><span></span><span></span></div>
</footer>
</body>
</html>
```